SaaS / Consulting / Solution website redesign

We need a website design that:
- Is completely different than our current design : https://plumvessel.net
- Has a very minimal amount of copy
- Changes our positioning from a SaaS application to a solutions company. Solutions company means that we help our customers solve their problems with consulting, training, and tools. An example of a solutions company is here: https://oldpages.example/web/20130111103320/http://www.brindlework.com:80/
- Does not make us look like a start up
- Is more people oriented than technology oriented

We need a designer that:
- Is a rebel at heart
- Is a minimalist
- Tells us why our current site sucks
- Can disagree with us
- Can also do copywriting or already has a copywriter that can help
- Is ok with saying we have capability that we don't in order to see if people actually want that
- Can understand the difference between our grand vision and where we need to focus ourselves today in order to get there

Who we are:
- Entrepreneurs
- Programmers
- Consultants
- Investors

Here's our design goals:
#1 Get customers, investors, employers, and partners excited about our unique and clearly articulated value proposition
#2 Get people to contact us asking for help with their programs
#3 Position ourselves as an expert in the skills based volunteering, mentorship, and group collaboration
#4 Make it easy for people, who already know who we are, to register online

What our grand vision is:
- Create a marketplace where any person can go to our site and find time with anyone they need to meet with. Whether that is their hair stylist, school advisor, parent of your kids class, dentist, attorney, etc.

What will you get if you win:
- In addition to the prize of this project we will have many landing pages and other revisions we will need in the future. We currently don't have a designer or copywriter and need to add that capability to our team

Who do we need to appeal to:
- Directors that are launching innovative programs inside organizations
- IT personnel who are trying to disqualify our technology so they don't have to support it or deal with it when it doesn't go well
- Enterprise IT architects who don't want our product being on its own island within their organization totally incompatible with everything else. Architects which are trying to assess how our platform will co-exist with all their other platforms
- Vice Presidents who want to help their directors understand that we don't have enough experience to help them
- Program managers who have to juggle a million things and need a tool that actually helps instead of confuses them and adds more work for them.
- Program managers & directors that have been given ambiguous goals by their board of directors like "improve retention, increase engagement, create innovation, get people to collaborate." And who have no idea where to start or how to deliver on things like that.
- Program managers, directors, and vice presidents that are trying to understand how our technology and services fit into their existing technology and capability
- Employees who are bored and uninspired with their current tools and are hoping for some excitement in their life. Kind of like candy or a double espresso.
- Investors who think, our company like all the rest, are going to waste their money and make them look like a fool

Other information:
-The CSS and html needs to be responsive

-Our registration onboarding flow needs to collect this information:
User first name
user last name
user email
(verify their email)
user phone number
(verify their phone number)
User profile image (optional)
User profile summary (optional, like a bio, freeform text fiels)
If applicable: Register their organization
Organization name
Organization image (optional)
Account Mailing address
account Billing address (could be same as mailing address)
account Billing email address (could be same as user address)
account Product selection (pricing tier)
account Credit card information

The designs I am getting are a good start but they are only the front page. I just want you to know that I am expecting and need more than a landing page to complete the design. I will likely need a page that outlines the benefits and features of the product itself, how its different than our competitors, which will not be on the front page. I will need a registration flow. I will need a blog page design so we can post blog articles, I will need a team page, a page that goes into detail on our training, our services. I will likely need a page that shows all news and media we have been in. I need to show customer and user quotes, case studies, a way to contact us, partners, general resources like on collaboration, product tutorials, customers. I need the site to address a comprehensive set of needs. I need that design to be consistent and thorough. I know what PlateHarbor is. I'm not using because I need more than a template that was customized. I need to be unique and match our brand thoughtfully, beautifully, and artistically. Someone asked me a question about how Murmly is similar to our tool in the way it is referred by end users and purchased by managers. Our website needs to primarily talk to the managers as I explained in the brief but it needs to appear cool and exciting to our end-users without focusing on the technology too much. Murmly is a tool that teams use to collaborate in small and large enterprises. The value prop for them is that communication is easier. But they don't put that on their website. Why? Because the users of the technology won't go to the website to find out information on it, they get their information from someone who is using it and demos it to them. When Ines tells her manager Otto "Lets get murmly, Ruth is using it at her company and its great" Ines's manager doesn't know anything about murmly so she promptly googles it. The most important thing from Ines's perspective is that Otto agrees to try it out. Otto's biggest concern is that productivity will be enhanced to degraded. Murmly knows this and so on the front page they know they are talking to Otto NOT Ines because Ines is already sold on it and doesn't need to get sold on the website. Ines is end user. Otto is the purchaser. We have the same problem and so our end users are not the ones purchasing our product, their managers are purchasing our product. We get referred by our end users and vetted by their managers. Hope this helps! Thank you for looking at this project!  Added Wednesday, June 7, 2017

Another observation I am having about the designs being submitted. I believe we used the animations on our current website because animations / cartoons connect with the "inner child" in our users. Whatever that means :-). I think it's what makes our brand fun. I have a hard time imagining that we could make the design fun looking without animations but I'm sure it can be achieved. I also recognize that blending pictures of real people and animations is hard. So either we must masterfully blend them, use only animations, or make the real people have a LOT of fun! So far most of the designs while achieve the goal of appealing to the serious Vice Presidents and directors, they are not doing a good job at appealing to the overworked program managers and bored employees. There seems to stand another challenge with animations which is animations are hard to find and/or create that achieve the message / emotion we are trying to communicate. I don't have any good answers for this but I will say we can hire both animators and illustrators if we need to. All you have to do is communicate the effect in the website design with some simpler version maybe not the end illustration or animation itself. Added Wednesday, June 7, 2017

• Sex appeal and a sense of humor. Copy that makes people excited and clairvoyant about our potential.
• Boring renditions of other non-inspiring websites

```html
<!DOCTYPE html>
<html lang="en">
<head>
<meta charset="utf-8">
<title>PlumVessel — Consulting, Training &amp; Tools</title>
<link href="https://fonts.googleapis.com/css2?family=Raleway:wght@300;400;500;600&display=swap" rel="stylesheet">
<style>
:root{
  --blue:#3fb0e8;
  --green:#7fd07f;
  --ink:#2f3338;
  --muted:#8a9096;
  --paper:#ffffff;
  --mist:#f4f5f7;
  --footer:#587180;
  --footer-ink:#dfe7ec;
}
*{box-sizing:border-box;margin:0;padding:0}
html,body{width:1200px;height:3383px;overflow:hidden}
body{font-family:"Raleway",sans-serif;color:var(--ink);background:var(--paper);position:relative}
.abs{position:absolute}
.btn{position:absolute;display:flex;align-items:center;justify-content:center;border-radius:24px;font-size:12px;font-weight:600;color:#fff;height:32px}
.btn--green{background:var(--green)}
.btn--blue{background:var(--blue)}
.btn--ghost{background:#fff;border:2px solid #e2e6ea;color:var(--blue)}

/* hero */
.hero{position:absolute;left:0;top:0;width:1200px;height:564px;background:linear-gradient(120deg,#8da3b4 0%,#c9d3da 45%,#e6ebee 70%,#b7c3cc 100%)}
.brand{position:absolute;display:flex;align-items:center;gap:8px;font-weight:500}
.brand__mark{width:34px;height:34px;border-radius:50%;border:3px solid currentColor}
.hero .brand{left:79px;top:30px;color:#fff;font-size:30px}
.callus{position:absolute;right:160px;top:24px;color:#fff;font-size:18px;white-space:nowrap}
.hero-icons{position:absolute;right:46px;top:14px;display:flex;gap:14px}
.hero-icons span{width:40px;height:40px;border-radius:50%;border:2px solid #fff;background:var(--green);display:flex;align-items:center;justify-content:center}
.nav{position:absolute;left:440px;top:84px;display:flex;gap:36px;font-size:12px;font-weight:600;color:#fff}
.nav .active{background:var(--blue);padding:7px 18px;border-radius:16px;margin-top:-7px}
.slider-arrows{position:absolute;left:150px;top:498px;display:flex;gap:8px}
.slider-arrows span{width:24px;height:24px;border-radius:50%;border:2px solid #fff}
.pitch{position:absolute;left:767px;top:203px;width:356px;height:411px;background:var(--blue);padding:42px 40px;color:#fff;z-index:2}
.pitch h1{font-weight:400;font-size:29px;line-height:1.22;width:270px}
.pitch .btn{left:40px;top:300px;width:200px;height:54px;border:3px solid #fff;border-radius:30px;font-size:13px;text-align:center;line-height:1.2}

/* connected */
.connected{position:absolute;left:0;top:564px;width:1200px;height:417px;background:var(--mist);text-align:center}
.connected h2{position:absolute;left:0;right:0;top:126px;font-size:23px;font-weight:400}
.ghost-word{position:absolute;top:178px;font-size:64px;font-weight:600;color:#fff;letter-spacing:4px}
.pillar{position:absolute;top:218px;width:260px;font-size:13px;color:var(--muted);line-height:1.3}
.pillar b{color:var(--blue);font-weight:500}
.connected .btn{left:527px;top:300px;width:126px;height:38px;font-size:11px}

/* audience rows */
.photo{position:absolute}
.row-title{position:absolute;font-size:23px;font-weight:400;line-height:1.28}
.row-copy{position:absolute;font-size:14px;color:var(--muted);line-height:1.5;width:335px}

/* banner */
.banner{position:absolute;left:0;top:1850px;width:1200px;height:239px;background:linear-gradient(90deg,#2f3c46,#5a6b77 60%,#40505b)}
.banner h3{position:absolute;left:153px;top:78px;font-size:29px;font-weight:400;color:#fff}
.banner p{position:absolute;left:153px;top:114px;font-size:18px;color:#fff;line-height:1.3;width:560px}
.banner .btn{left:896px;top:100px;width:150px;height:40px}

/* goals */
.goals h2{position:absolute;left:0;right:0;top:2162px;text-align:center;font-size:23px;font-weight:400;line-height:1.35}
.goal{position:absolute;top:2266px;width:220px;text-align:center;font-size:13px;color:var(--muted)}
.goal__ring{width:100px;height:100px;border-radius:50%;border:2px solid var(--blue);margin:0 auto 16px;display:flex;align-items:center;justify-content:center}
.goal--on .goal__ring{background:var(--blue)}

/* testimonials */
.voices{position:absolute;left:0;top:2474px;width:1200px;height:627px;background:var(--mist);text-align:center}
.voices h2{position:absolute;left:0;right:0;top:76px;font-size:23px;font-weight:400}
.quote{position:absolute;left:250px;width:700px;top:140px;font-size:14px;line-height:1.55;color:var(--muted)}
.quote .mk{color:var(--blue);font-weight:600}
.arrow-ring{position:absolute;top:150px;width:26px;height:26px;border-radius:50%;border:2px solid #c9cfd4}
.divider{position:absolute;left:153px;right:153px;top:250px;height:1px;background:#dde1e5}
.client{position:absolute;top:300px;height:70px;width:128px;background:#fff;display:flex;align-items:center;justify-content:center;font-size:20px;font-weight:600;color:#9aa1a7}
.client--featured{top:283px;height:110px;width:180px}
.crowd{position:absolute;left:0;top:424px;width:1200px;height:203px;background:linear-gradient(180deg,var(--mist),#c8ccd0 70%,#9da3a8)}

/* footer */
.footer{position:absolute;left:0;top:3101px;width:1200px;height:282px;background:var(--footer);color:var(--footer-ink);font-size:13px}
.footer .brand{left:153px;top:70px;font-size:26px;color:#fff}
.footer .legal{position:absolute;left:153px;top:122px;line-height:1.45}
.footer ul{position:absolute;list-style:none;line-height:1.65}
.footer ul .on{color:var(--blue)}
.footer address{position:absolute;left:841px;top:76px;font-style:normal;line-height:1.45}
.footer address .phone{font-size:20px;color:#fff}
.social{position:absolute;left:1060px;top:80px;display:flex;flex-direction:column;gap:12px;font-size:12px;color:#fff}
.social li{display:flex;align-items:center;gap:8px;list-style:none}
.social i{width:26px;height:26px;border-radius:50%;border:2px solid #fff;display:block}
.social .on i{background:var(--blue)}
.to-top{position:absolute;left:1134px;top:-22px}
</style>
</head>
<body>

<header class="hero">
  <div class="abs" role="img" aria-label="Photo of colleagues shaking hands across a table in a bright office" style="inset:0"></div>
  <div class="brand"><span class="brand__mark"></span>PlumVessel</div>
  <div class="callus">Call us @ &nbsp;+1-800-555-0147</div>
  <div class="hero-icons">
    <span><svg width="16" height="12" viewBox="0 0 16 12"><rect x="1" y="1" width="14" height="10" fill="none" stroke="#fff" stroke-width="1.5"/><path d="M1 1l7 6 7-6" fill="none" stroke="#fff" stroke-width="1.5"/></svg></span>
    <span><svg width="14" height="16" viewBox="0 0 14 16"><rect x="1" y="7" width="12" height="8" fill="none" stroke="#fff" stroke-width="1.5"/><path d="M4 7V4a3 3 0 0 1 6 0v3" fill="none" stroke="#fff" stroke-width="1.5"/></svg></span>
  </div>
  <nav class="nav">
    <span class="active">Company</span><span>Products</span><span>Solutions</span><span>Services &amp; Support</span><span>Industries</span><span>Contact Us</span>
  </nav>
  <div class="slider-arrows"><span></span><span></span></div>
</header>

<section class="pitch">
  <h1>Vice Presidents who wants to help directors but don't have enough experience to help them!</h1>
  <span class="btn btn--green">Get 30 Min. Free<br>Consultancy</span>
</section>

<section class="connected">
  <h2>Get Connected with PlumVessel for</h2>
  <span class="ghost-word" style="left:200px">WHAT</span>
  <span class="ghost-word" style="left:520px">HOW</span>
  <span class="ghost-word" style="left:800px">WHY</span>
  <p class="pillar" style="left:165px">We're <b>building software</b> that connects people in person</p>
  <p class="pillar" style="left:470px">We're <b>fixing this</b> by connecting people in person</p>
  <p class="pillar" style="left:775px">People are becoming <b>more isolated</b> than connected because of technology</p>
  <span class="btn btn--blue">Explore More</span>
</section>

<section class="audiences">
  <div class="photo" role="img" aria-label="Photo of two smiling businessmen reviewing a tablet" style="left:230px;top:1065px;width:282px;height:320px;background:linear-gradient(135deg,#d9dee2,#7d8c99 60%,#3e4a55)"></div>
  <h3 class="row-title" style="left:614px;top:1090px;width:360px">Management - Looking to Launch Innovative Programs inside Organizations</h3>
  <p class="row-copy" style="left:614px;top:1203px">Consult to know how our technology and services fit into their existing technology and capability lorem ipsum has ...</p>
  <span class="btn btn--ghost" style="left:614px;top:1316px;width:86px">More</span>
  <span class="btn btn--green" style="left:713px;top:1316px;width:130px">Consult Now</span>

  <h3 class="row-title" style="left:230px;top:1460px;width:335px">Bored and Uninspired Employees with their current tools &amp; are hoping for some excitement in their life</h3>
  <p class="row-copy" style="left:230px;top:1598px;width:330px">Choose candy/double espresso and consult for more lorem ipsum ...</p>
  <span class="btn btn--ghost" style="left:230px;top:1686px;width:86px">More</span>
  <span class="btn btn--green" style="left:329px;top:1686px;width:130px">Consult Now</span>
  <div class="photo" role="img" aria-label="Photo of a tired man at a laptop surrounded by crumpled paper" style="left:688px;top:1435px;width:284px;height:320px;background:linear-gradient(135deg,#c8a98a,#8a7868 55%,#4a4f55)"></div>
</section>

<section class="banner" role="img" aria-label="Photo of investors in a meeting, darkened behind the text">
  <h3>Investors who think,</h3>
  <p>our company like all the rest, are going to waste their money and make them look like a fool!</p>
  <span class="btn btn--green">Contact Us</span>
</section>

<section class="goals">
  <h2>Program managers &amp; directors with ambiguous<br>goals by their board of directors as:</h2>
  <div class="goal" style="left:147px"><div class="goal__ring"><svg width="40" height="40" viewBox="0 0 40 40" fill="none" stroke="#3fb0e8" stroke-width="2"><circle cx="20" cy="20" r="15"/><circle cx="20" cy="16" r="5"/><path d="M11 28c3-5 15-5 18 0"/></svg></div>Improve Retention</div>
  <div class="goal goal--on" style="left:375px"><div class="goal__ring"><svg width="40" height="40" viewBox="0 0 40 40" fill="none" stroke="#fff" stroke-width="2.5"><path d="M24 10l-11 11a4 4 0 0 0 6 6l12-12a6 6 0 0 0-9-9L10 18"/></svg></div>Increase Engagement</div>
  <div class="goal" style="left:603px"><div class="goal__ring"><svg width="40" height="40" viewBox="0 0 40 40" fill="none" stroke="#3fb0e8" stroke-width="2"><path d="M15 24a8 8 0 1 1 10 0v4H15z"/><path d="M16 32h8M20 6V3M8 12l-2-2M32 12l2-2"/></svg></div>Create Innovation</div>
  <div class="goal" style="left:833px"><div class="goal__ring"><svg width="44" height="40" viewBox="0 0 44 40" fill="#3fb0e8"><circle cx="22" cy="13" r="5"/><circle cx="11" cy="16" r="4"/><circle cx="33" cy="16" r="4"/><path d="M13 32c0-8 18-8 18 0zM3 32c0-6 11-7 12-3v3zM41 32c0-6-11-7-12-3v3z"/></svg></div>Get People to Collaborate</div>
</section>

<section class="voices">
  <h2>What our client says?</h2>
  <span class="arrow-ring" style="left:150px"></span>
  <p class="quote"><span class="mk">&#8220;</span> Running my ideas by seasoned mentors has proven instrumental to Kestrelo's progress. PlumVessel lets me quickly schedule these meetings without a headache so I can get back to launching my startup. Lorem Ipsum has been the industry's standard <span class="mk">&#8221;</span></p>
  <span class="arrow-ring" style="left:1022px;border-color:var(--green)"></span>
  <div class="divider"></div>
  <div class="client" style="left:230px">Northvale</div>
  <div class="client" style="left:372px">Ember</div>
  <div class="client client--featured" style="left:510px;color:var(--blue)">Brightbulb</div>
  <div class="client" style="left:700px">Ferro</div>
  <div class="client" style="left:842px">Lantern</div>
  <div class="crowd" role="img" aria-label="Black and white photo of many raised hands giving thumbs up"></div>
</section>

<footer class="footer">
  <svg class="to-top" width="20" height="22" viewBox="0 0 20 22" fill="none" stroke="#7fd07f" stroke-width="2"><path d="M10 21V3M3 10l7-7 7 7"/></svg>
  <div class="brand"><span class="brand__mark" style="color:var(--green)"></span>PlumVessel</div>
  <p class="legal">© 2016 PlumVessel Inc.<br>All rights reserved</p>
  <ul style="left:383px;top:74px"><li>Company</li><li class="on">Products</li><li>Solutions</li><li>Services &amp; Support</li><li>Industries</li><li>Blog</li><li>Press</li></ul>
  <ul style="left:609px;top:74px"><li>Privacy</li><li>Legal</li><li>Data Transfers</li><li>Contact Us</li><li>Site Map</li></ul>
  <address>PlumVessel Inc.<br>48 Larkin Row, Eastbrook,<br>RI 02811<br><br>Contact Us<br><span class="phone">+1-800-555-0147</span><br>info@plumvessel.net</address>
  <ul class="social"><li><i></i>Chirp</li><li class="on"><i></i>Gather</li><li><i></i>Linkwork</li></ul>
</footer>

</body>
</html>
```